Leading Financial Advisory Firm Needs a Web Redesign

Job Type
Web Redesign

Task Outline
Create an Updated Web Design for our existing web site

Task Description
Dunmore Kestrel Group Inc. is a leading financial advisory firm to the global steel, metals and mining sectors. We are seeking a web designer to refashion, freshen and update the look of our existing website. The substance of the revised website should reflect our updated Credentials attached.

Our existing web site has an outdated “look”; it was originally put together quickly from an earlier PowerPoint presentation of our Credentials. We do not want the revised web site to look like a PowerPoint presentation which has been put up online. Rather, with a designer’s help, we would like to refashion the pages so that the look and feel of the site is consistent with a professional service organization's site. We are not interested in any significant changes in substance, just in format. There should also be no changes to the design/font/color of the “Dunmore Kestrel” logo.

The final selected designer will be responsible for all design and coding/programming responsibilities subject to our approval. The revised site should be done in Word Press or similar "user-friendly" application so that we can make edits afterwards.

A few specific changes:
• Textual changes:
• Wherever it currently says Dunmore Kestrel is an “affiliate” of Orvanne, this should be replaced with “Broker Dealer related services provided through Orvanne Partners LLC”; this appears on the copyright info on the bottom of each page;
• Please also add this telephone number to the 212 number listed: 917-555-0183;
• The text on the “About Us” tab needs to be updated as follows: “We currently have active steel, metals and mining assignments in Europe, South Africa, Australia and Ukraine.”
• The Services tab under Core Services currently says “Capital Raising (through affiliates)”; it should say “Capital Raising (through broker dealers)”;
• Our firm name in the Contacts tab should be “Dunmore Kestrel Group Inc.”
• Tara Wendle’ bio should be removed from the Bios tab;
• The map in the Global Scope and Perspective tab should be replaced with the map in the attached updated Credentials (see slide 11)

Very truly yours,

Dunmore Kestrel Group Inc.

Our current website is: http://www.dunmorekestrel.example

Deadline
5 Days

Target Market(s)
Companies in the steel, metals and mining sectors interested in financial advisory services and/or strategic and/or financial partners.

Industry/Entity Type

Financial

```html
<!DOCTYPE html>
<html lang="en">
<head>
<meta charset="utf-8">
<title>Dunmore Kestrel — Financial Advisory</title>
<link href="https://fonts.googleapis.com/css2?family=Open+Sans:wght@400;600;700&display=swap" rel="stylesheet">
<style>
:root{
  --green-dark:#1f5200;
  --green:#2e6e07;
  --green-mid:#3d8a12;
  --green-light:#5a9e2a;
  --btn-green:#0b5a12;
  --ink:#222;
  --muted:#555;
  --soft:#f6f6f6;
  --rule:#d8d8d8;
  --footer:#111;
}
*{margin:0;padding:0;box-sizing:border-box}
html,body{width:1200px;height:2365px;overflow:hidden}
body{position:relative;background:#fff;font-family:"Open Sans",Arial,sans-serif;color:var(--ink)}
.abs{position:absolute}

.top-bar{left:0;top:0;width:1200px;height:16px;background:var(--green-dark)}
.top-stripe{left:0;top:16px;width:1200px;height:8px;background:var(--green-light)}
.header{left:0;top:24px;width:1200px;height:165px;background:linear-gradient(#fff,#e6e6e6)}
.brand{left:188px;top:66px;color:var(--ink);font-weight:600;font-size:22px;letter-spacing:.5px}
.phone{left:880px;top:68px;display:flex;align-items:center;gap:10px;font-weight:700;font-size:18px;color:#333}
.phone-ico{width:34px;height:34px;border-radius:50%;background:#bbb;display:flex;align-items:center;justify-content:center}
.nav{left:172px;top:147px;height:39px;display:flex;font-size:11.5px;text-transform:uppercase;color:#222}
.nav a{display:flex;align-items:center;padding:0 16px;color:inherit;text-decoration:none}
.nav a.active{background:var(--green);color:#fff;padding:0 19px}
.nav-rule{left:0;top:186px;width:1200px;height:3px;background:var(--green-mid)}

.hero{left:0;top:189px;width:1200px;height:505px;background:radial-gradient(ellipse at center,#3f8a12 0%,#2a6a05 70%,#235c03 100%)}
.hero-edge{left:0;top:686px;width:1200px;height:8px;background:var(--green-light)}
.slide{left:172px;top:219px;width:856px;height:387px;background:radial-gradient(ellipse at 72% 45%,#ffc24a 0%,#e0661a 22%,#5b2a10 55%,#1b120c 100%);box-shadow:0 18px 24px rgba(0,0,0,.35)}
.slide-caption{left:172px;top:481px;height:125px;background:rgba(0,0,0,.72);color:#fff;font-weight:700;font-size:20px;line-height:32px;padding:27px 27px;white-space:nowrap}
.dots{left:543px;top:646px;display:flex;gap:18px}
.dots span{width:14px;height:14px;border-radius:50%;background:radial-gradient(circle at 40% 35%,#fff,#bbb)}

.feature{top:735px;width:262px;height:147px;background:linear-gradient(#1b7a1c,#054f0a);color:#fff;font-weight:700;font-size:15px;text-transform:uppercase;text-align:center}
.feature svg{position:absolute;left:50%;top:38px;transform:translateX(-50%)}
.feature span{position:absolute;left:0;right:0;top:104px}

.welcome-bg{left:0;top:922px;width:1200px;height:365px;background:var(--soft);border-top:1px solid #eee;border-bottom:1px solid #e6e6e6}
.sec-title{height:37px;border-bottom:3px solid var(--rule);border-left:8px solid var(--green);padding-left:14px;font-weight:700;font-size:15px;text-transform:uppercase;line-height:34px}
.welcome-text{left:181px;top:1015px;width:548px;font-size:11.5px;line-height:21px;color:#555}
.welcome-text b{color:var(--green);font-weight:400}
.dashed{left:181px;top:1099px;width:520px;border-top:1px dashed #ccc}
.checks{left:200px;top:1114px;list-style:none;font-size:13px;color:#333}
.checks li{height:27px;display:flex;align-items:center;gap:10px}
.btn{top:1217px;height:35px;font-size:11.5px;text-transform:uppercase;color:#fff;display:flex;align-items:center;justify-content:center}
.btn-primary{left:181px;width:109px;background:var(--btn-green)}
.btn-dark{left:301px;width:109px;background:linear-gradient(#555,#222)}
.video{left:744px;top:1044px;width:284px;height:196px;background:linear-gradient(135deg,#8fa4ae,#3c4a56 55%,#1c2630)}

.list{left:200px;top:1385px;list-style:none;font-size:13px;color:#333}
.list li{height:31px;display:flex;align-items:center;gap:12px}
.list li i{width:10px;height:10px;border-radius:50%;border:3px solid #222;display:block}
.news{left:457px;width:280px;height:80px}
.news .thumb{position:absolute;left:0;top:0;width:106px;height:76px}
.news p{position:absolute;left:118px;top:-4px;width:165px;font-size:12.5px;line-height:20px;color:#333}
.news small{display:block;font-size:10px;color:#999}
.quote{left:754px;top:1386px;width:268px;height:175px;background:#fff;border:1px solid #ddd;border-radius:3px;padding:40px 28px;font-size:11.5px;line-height:20px;color:#555}
.quote::before{content:"\201C";position:absolute;left:26px;top:4px;font-size:38px;color:#ccc}
.quote::after{content:"";position:absolute;left:40px;bottom:-9px;width:16px;height:16px;background:#fff;border-right:1px solid #ddd;border-bottom:1px solid #ddd;transform:rotate(45deg)}
.cite{left:770px;top:1580px;font-size:11px;color:#444;line-height:25px}
.cite b{display:block;color:#333}
.pager{display:flex;gap:7px}
.pager span{width:8px;height:8px;border-radius:50%;background:#888}
.pager span.on{background:var(--green)}

.projects-bg{left:0;top:1687px;width:1200px;height:363px;background:var(--soft);border-top:1px solid #eee;border-bottom:1px solid #e6e6e6}
.arrows{display:flex;gap:10px}
.arrows span{width:26px;height:26px;border-radius:50%;display:flex;align-items:center;justify-content:center}
.card{top:1809px;width:271px;height:205px;background:#e9e8e8}
.card .img{position:absolute;left:20px;top:17px;width:228px;height:114px}
.card p{position:absolute;left:20px;top:144px;font-size:12.5px;color:#333}
.card small{position:absolute;left:27px;top:175px;font-size:9.5px;color:#555}

.clients-title{left:180px;top:2106px;font-weight:700;font-size:14px}
.client{top:2168px;height:46px;display:flex;align-items:center;justify-content:center;font-weight:700;font-size:14px}

.footer{left:0;top:2266px;width:1200px;height:99px;background:var(--footer);border-top:3px solid var(--green)}
.foot-links{left:180px;top:2296px;font-size:11px;color:#ccc}
.foot-copy{left:180px;top:2326px;font-size:10px;color:#888}
.social{left:858px;top:2303px;display:flex;gap:8px}
.social span{height:30px;padding:0 8px;border-radius:4px;background:#1a6fb3;color:#fff;font-size:11px;display:flex;align-items:center}
</style>
</head>
<body>
<div class="abs top-bar"></div>
<div class="abs top-stripe"></div>
<header class="abs header"></header>
<div class="abs brand">Dunmore Kestrel</div>
<div class="abs phone"><span class="phone-ico"><svg width="16" height="16" viewBox="0 0 24 24"><path fill="#fff" d="M6.6 10.8a15 15 0 0 0 6.6 6.6l2.2-2.2a1 1 0 0 1 1-.25 11.4 11.4 0 0 0 3.6.6 1 1 0 0 1 1 1V20a1 1 0 0 1-1 1A17 17 0 0 1 3 4a1 1 0 0 1 1-1h3.5a1 1 0 0 1 1 1c0 1.25.2 2.45.6 3.6a1 1 0 0 1-.25 1z"/></svg></span>212.555.0147</div>
<nav class="abs nav">
  <a class="active">Home</a><a>About Us</a><a>Services</a><a>Representative Engagements</a><a>Global Scope and Perspective</a><a>Bios</a><a>Contact Us</a>
</nav>
<div class="abs nav-rule"></div>

<section class="abs hero"></section>
<div class="abs hero-edge"></div>
<div class="abs slide" role="img" aria-label="Hot steel coil glowing in a rolling mill"></div>
<div class="abs slide-caption">Broker Dealer related services<br>provided through Orvanne Partners LLC</div>
<div class="abs dots"><span></span><span></span><span></span><span></span></div>

<div class="abs feature" style="left:208px">
  <svg width="48" height="52" viewBox="0 0 48 52"><path d="M24 2 44 9v15c0 13-9 21-20 26C13 45 4 37 4 24V9z" fill="none" stroke="#fff" stroke-width="4"/><rect x="21.5" y="14" width="5" height="16" fill="#fff"/><rect x="21.5" y="34" width="5" height="5" fill="#fff"/></svg>
  <span>Strategic Advice</span>
</div>
<div class="abs feature" style="left:472px">
  <svg width="48" height="48" viewBox="0 0 48 48" fill="#fff"><path d="M4 4l14 14v-9h4v16H6v-4h9L1 7z"/><path d="M44 4 30 18v-9h-4v16h16v-4h-9L47 7z"/><path d="M4 44l14-14v9h4V23H6v4h9L1 41z"/><path d="M44 44 30 30v9h-4V23h16v4h-9l14 14z"/></svg>
  <span>Mergers &amp; Acquisitions</span>
</div>
<div class="abs feature" style="left:735px">
  <svg width="50" height="46" viewBox="0 0 50 46" fill="#fff"><rect x="2" y="24" width="12" height="20"/><rect x="18" y="14" width="12" height="30"/><rect x="34" y="2" width="12" height="42"/></svg>
  <span>Capital Raising</span>
</div>

<section class="abs welcome-bg"></section>
<h2 class="abs sec-title" style="left:172px;top:962px;width:557px">Welcome to Dunmore Kestrel</h2>
<p class="abs welcome-text">Phasellus lacinia commodo arcu, vitae posuere nulla malesuada quis. <b>Vivamus dapibus nisl ac lacus</b> volutpat mollis sagittis quam gravida. <b>Morbi consequat</b> ipsum at libero interdum at varius magna auctor. Phasellus lacinia commodo arcu, <b>vitae posuere nulla dapibus</b> nisl ac lacus volutpat.</p>
<div class="abs dashed"></div>
<ul class="abs checks">
  <li><svg width="14" height="12" viewBox="0 0 14 12"><path d="M1 6l4 4 8-9" fill="none" stroke="#2e6e07" stroke-width="2"/></svg>Maecenas vitae ipsum quis magna vestibulum mollis.</li>
  <li><svg width="14" height="12" viewBox="0 0 14 12"><path d="M1 6l4 4 8-9" fill="none" stroke="#2e6e07" stroke-width="2"/></svg>Nunc vulputate massa non lectus porttitor viverra quis eu augue.</li>
  <li><svg width="14" height="12" viewBox="0 0 14 12"><path d="M1 6l4 4 8-9" fill="none" stroke="#2e6e07" stroke-width="2"/></svg>Nullam feugiat lacus id augue congue nec mollis ligula aliquam.</li>
</ul>
<a class="abs btn btn-primary">Read More</a>
<a class="abs btn btn-dark">Contact Us</a>
<div class="abs video" role="img" aria-label="Video still of business advisors in conversation outdoors"></div>
<svg class="abs" style="left:858px;top:1113px" width="60" height="60" viewBox="0 0 60 60"><circle cx="30" cy="30" r="28" fill="#d02a2a" opacity=".85"/><path d="M24 18v24l19-12z" fill="#fff"/></svg>

<h2 class="abs sec-title" style="left:172px;top:1333px;width:277px">Mining Expertise</h2>
<ul class="abs list">
  <li><i></i>Iron Ore</li><li><i></i>Platinum</li><li><i></i>Uranium</li><li><i></i>Coal</li><li><i></i>Gold</li><li><i></i>Bauxite</li><li><i></i>Copper</li><li><i></i>Silver</li><li><i></i>Manganese</li>
</ul>

<h2 class="abs sec-title" style="left:457px;top:1333px;width:278px">Latest News</h2>
<div class="abs news" style="top:1391px"><div class="thumb" role="img" aria-label="Industrial refinery towers under blue sky" style="background:linear-gradient(#7aa6d6,#5c6c78)"></div><p>At vero eos et accusamus et iusto odio dignissimos ducimus .<small>Mar 28,2014</small></p></div>
<div class="abs news" style="top:1485px"><div class="thumb" role="img" aria-label="Molten metal glowing in a dark furnace" style="background:radial-gradient(circle at 50% 55%,#f3c35a,#5a2c0c 55%,#1a0e06)"></div><p>At vero eos et accusamus et iusto odio dignissimos ducimus .<small>Mar 28,2014</small></p></div>
<div class="abs news" style="top:1580px"><div class="thumb" role="img" aria-label="Stacks of steel bars in a warehouse" style="background:linear-gradient(135deg,#9aa3a8,#4a5258)"></div><p>At vero eos et accusamus et iusto odio dignissimos ducimus .<small>Mar 28,2014</small></p></div>

<h2 class="abs sec-title" style="left:744px;top:1333px;width:278px">Testmonials</h2>
<div class="abs pager" style="left:962px;top:1346px"><span></span><span class="on"></span><span></span></div>
<blockquote class="abs quote">One of the world's premier investment banks to the steel, metals, and mining industries</blockquote>
<div class="abs cite"><b>Harlan J. Medford</b>Managing Partner of Ironline Metals Research</div>

<section class="abs projects-bg"></section>
<h2 class="abs sec-title" style="left:172px;top:1725px;width:856px">Recent Projects</h2>
<div class="abs arrows" style="left:965px;top:1730px">
  <span style="background:#555"><svg width="10" height="10" viewBox="0 0 10 10"><path d="M7 1 2 5l5 4z" fill="#fff"/></svg></span>
  <span style="background:var(--btn-green)"><svg width="10" height="10" viewBox="0 0 10 10"><path d="M3 1l5 4-5 4z" fill="#fff"/></svg></span>
</div>
<div class="abs card" style="left:180px"><div class="img" role="img" aria-label="Steel mill interior with coils" style="background:linear-gradient(135deg,#b8bcc0,#4b5054)"></div><p>Lorem ipsum dolor sit amet,</p><small>24 Jan 2014</small></div>
<div class="abs card" style="left:462px"><div class="img" role="img" aria-label="Illuminated steel plant at night" style="background:radial-gradient(ellipse at 50% 40%,#e08a3a,#5a2412 60%,#1a0c08)"></div><p>Lorem ipsum dolor sit amet,</p><small>24 Jan 2014</small></div>
<div class="abs card" style="left:755px"><div class="img" role="img" aria-label="Sparks flying from molten steel" style="background:radial-gradient(ellipse at 55% 50%,#f0a040,#6a2a0c 45%,#120a06)"></div><p>Lorem ipsum dolor sit amet,</p><small>24 Jan 2014</small></div>

<h2 class="abs clients-title">OUR CLIENTS</h2>
<div class="abs arrows" style="left:965px;top:2100px">
  <span style="background:#555"><svg width="10" height="10" viewBox="0 0 10 10"><path d="M7 1 2 5l5 4z" fill="#fff"/></svg></span>
  <span style="background:var(--btn-green)"><svg width="10" height="10" viewBox="0 0 10 10"><path d="M3 1l5 4-5 4z" fill="#fff"/></svg></span>
</div>
<div class="abs client" style="left:194px;width:143px;background:#888;color:#fff">Varnholt</div>
<div class="abs client" style="left:376px;width:138px;background:#555;color:#fff">Qinlan Steel</div>
<div class="abs client" style="left:540px;width:150px;color:#333">Southreach Ore</div>
<div class="abs client" style="left:726px;width:138px;background:#999;color:#fff;font-size:11px">Tressell Steel Holdings</div>
<div class="abs client" style="left:893px;width:90px;height:28px;top:2177px;background:#333;color:#ddd;font-size:11px">Calder Gold</div>

<footer class="abs footer"></footer>
<div class="abs foot-links">Home &nbsp;|&nbsp; Disclaimer &nbsp;|&nbsp; Terms and Conditions &nbsp;|&nbsp; Privacy Policy &nbsp;|&nbsp; About Us &nbsp;|&nbsp; Contact</div>
<div class="abs foot-copy">Copyright © 2014 dunmorekestrel. all right reserved.</div>
<div class="abs social"><span>Sharebook</span><span>Chirper</span><span>Circlet</span><span>Linkway</span></div>
</body>
</html>
```